Summit Builders Web Site / Business Cards

Construction Company that specializes in Water and Fire Damage, Residential ReModels, Landscaping and Building ADU (Accessory Dwelling Unit)

Growing and changing families often need additional space, and a remodeling project can often provide that. Adding a new area, or repurposing an existing one can satisfy this requirement.

Other times, homeowners want to update the look in their kitchen or bathroom with more than just a change of cabinetry or vanity doors and drawers. Whatever your needs are, Summit Builders has skilled workers who are bonded and insured, and ready to make your dreams and visions a reality.

Target Market(s)

Home Owners

Industry/Entity Type

Construction Company

Contact Information for Business Card

Center Logo with our information on the corners

Back side to be Logo Only
Contact Info
CSLB License # 2418596
info@summitbuildersca.example
www.summitbuildersca.example

Coding

Coded - Design and coding required

Number of Pages Required

5+ page

Font styles to use
Serif
Sans Serif

Requirements
Must have
• Using our Logo Colors
Home
About Us
Services
Projects / Portfolio
Contact Us
Nice to have
• Colors matching our Logo
Should not have
• Black because it doesnt match our logo

```html
<!DOCTYPE html>
<html lang="en">
<head>
<meta charset="utf-8">
<title>Summit Builders</title>
<link href="https://fonts.googleapis.com/css2?family=Montserrat:wght@400;500;600;700&family=Open+Sans:wght@400;600&display=swap" rel="stylesheet">
<style>
:root{
  --orange:#f55a14;
  --orange-dark:#e04a0a;
  --navy:#1c2b6e;
  --navy-deep:#17245e;
  --ink:#1f2747;
  --text:#6b6f7e;
  --light:#f1f1f3;
  --white:#ffffff;
}
*{margin:0;padding:0;box-sizing:border-box}
html,body{width:1200px;height:4488px;overflow:hidden}
body{position:relative;background:var(--white);font-family:"Open Sans",sans-serif;color:var(--text)}
.abs{position:absolute}
h1,h2,h3,h4{font-family:"Montserrat",sans-serif;font-weight:500;color:var(--ink)}

/* header */
.topbar{left:645px;top:0;width:555px;height:52px;background:var(--orange);clip-path:polygon(28px 0,100% 0,100% 100%,46px 100%);color:var(--white);font-family:"Montserrat",sans-serif;font-size:12px;font-weight:500;display:flex;align-items:center;padding-left:58px;gap:10px;white-space:nowrap}
.topline{left:0;top:0;width:660px;height:3px;background:var(--navy)}
.brand{display:flex;align-items:center;gap:10px}
.brand-mark{width:30px;height:30px;background:var(--navy)}
.brand-name{font-family:"Montserrat",sans-serif;font-weight:700;color:var(--navy);font-size:24px;letter-spacing:1px;white-space:nowrap}
.header-brand{left:111px;top:60px}
.mainnav{left:450px;top:92px;display:flex;gap:40px;font-family:"Montserrat",sans-serif;font-size:13px;font-weight:500;color:var(--ink)}
.mainnav .active{color:var(--orange)}

/* hero */
.hero-edge{left:0;top:145px;width:1200px;height:786px;background:var(--orange);clip-path:polygon(0 0,100% 0,100% 77%,50% 100%,0 77%)}
.hero{left:0;top:145px;width:1200px;height:778px;background:linear-gradient(120deg,#6d4a35 0%,#9a7a5e 30%,#c7b7a0 55%,#8d8a86 80%,#b9b3ab 100%);clip-path:polygon(0 0,100% 0,100% 77%,50% 100%,0 77%)}
.hero-title{left:111px;top:350px;color:var(--white);font-family:"Montserrat",sans-serif;font-weight:600;line-height:1.05}
.hero-title .l1{font-size:68px;display:block}
.hero-title .l2{font-size:42px;display:block;margin-top:8px}
.btn{background:var(--orange);color:var(--white);font-family:"Montserrat",sans-serif;font-weight:600;font-size:14px;display:flex;align-items:center;justify-content:center;border-radius:3px}
.hero-btn{left:111px;top:511px;width:145px;height:54px}
.dots{left:573px;top:876px;display:flex;gap:6px}
.dots span{width:13px;height:13px;border-radius:50%;background:var(--white)}
.dots span.on{background:var(--orange)}

/* section titles */
.sec-title{width:1200px;text-align:center;font-size:35px;font-weight:500;color:var(--ink);letter-spacing:.5px}
.sec-rule{left:574px;width:52px;height:3px;background:var(--orange)}

/* service cards */
.card{width:313px;height:406px}
.card-photo{width:313px;height:242px}
.card-icon{position:absolute;left:0;top:172px;width:70px;height:70px;background:var(--orange);display:flex;align-items:center;justify-content:center}
.card-body{position:absolute;left:0;top:242px;width:313px;height:164px;padding:22px 0 0 0}
.card h3{font-size:20px;margin-bottom:12px}
.card p{font-size:12px;line-height:24px}
.readmore{margin-top:10px;color:var(--orange);font-family:"Montserrat",sans-serif;font-size:13px;font-weight:600;display:flex;align-items:center;gap:10px}
.card.active .card-body{background:var(--navy);padding-left:12px}
.card.active .card-icon{background:var(--navy)}
.card.active h3,.card.active p,.card.active .readmore{color:var(--white)}

/* who we are */
.who{left:0;top:1972px;width:1200px;height:568px;background:var(--light)}
.who-photo{left:0;top:1972px;width:592px;height:568px;background:linear-gradient(135deg,#c9c8c4 0%,#e3e1dc 45%,#d4a07c 70%,#bfc3c9 100%)}
.who-title{left:627px;top:2032px;font-size:35px}
.who-lead{left:627px;top:2112px;width:460px;font-size:13.5px;line-height:28px}
.feature{left:627px;width:460px;display:flex;gap:24px}
.feature-icon{width:100px;height:100px;border-radius:50%;background:var(--orange);flex:none;display:flex;align-items:center;justify-content:center}
.feature h4{font-size:14.5px;font-weight:700;margin-top:12px;margin-bottom:8px}
.feature p{font-size:13px;line-height:26px}

/* projects */
.proj{width:321px;height:261px}
.proj-fill{width:100%;height:100%}

/* clients */
.clients{left:0;top:3275px;width:1200px;height:505px;background:#f4f5f7}
.review{top:3428px;width:474px;height:262px;background:var(--white);border:1px solid #e3e3e6;box-shadow:0 2px 6px rgba(28,43,110,.06);padding:28px 30px}
.review-head{display:flex;align-items:center;gap:24px}
.avatar{width:104px;height:104px;border-radius:50%;background:radial-gradient(circle at 50% 40%,#c9a48a,#8a6a57);flex:none}
.review-head h4{font-size:18px;font-weight:500}
.role{color:var(--orange);font-size:13px;margin-top:8px}
.stars{margin-left:auto;color:var(--orange);font-size:14px;letter-spacing:2px;align-self:flex-start;margin-top:28px}
.review-body{display:flex;gap:16px;margin-top:18px}
.quote{color:var(--orange);font-family:"Montserrat",sans-serif;font-weight:700;font-size:72px;line-height:.8;height:40px}
.review-body p{font-size:13px;line-height:29px;text-align:justify}

/* stats */
.stats{left:0;top:3780px;width:1200px;height:195px;background:var(--orange)}
.stat{top:3830px;width:260px;text-align:center;color:var(--white);font-family:"Montserrat",sans-serif}
.stat b{display:block;font-size:48px;font-weight:500;line-height:1}
.stat span{display:block;font-size:16px;font-weight:500;margin-top:12px}

/* footer */
.footer{left:0;top:3975px;width:1200px;height:513px;background:var(--navy)}
.footnav{top:4032px;left:0;width:1200px;display:flex;justify-content:center;font-family:"Montserrat",sans-serif;font-size:12px;font-weight:500;color:var(--white)}
.footnav span{margin:0 36px}
.foot-rule{left:111px;top:4102px;width:978px;height:1px;background:rgba(255,255,255,.15)}
.foot-title{color:var(--white);font-size:22px;font-weight:500}
.field{background:var(--white);height:35px;font-size:11px;color:#555;padding:10px 12px;border:1px solid #d9d9d9}
.submit{left:111px;top:4343px;width:98px;height:33px;font-size:12px;border-radius:0}
.info{left:554px;display:flex;gap:18px;align-items:center;color:var(--white)}
.info-icon{width:43px;height:43px;border-radius:50%;border:2px solid var(--white);display:flex;align-items:center;justify-content:center;flex:none}
.info h5{font-family:"Montserrat",sans-serif;font-size:12px;font-weight:600}
.info p{font-size:11.5px;opacity:.85;margin-top:4px}
.foot-brand{left:846px;top:4138px;width:250px;display:flex;flex-direction:column;align-items:center}
.foot-brand .brand-mark{width:58px;height:58px;background:var(--white);margin-bottom:22px}
.foot-brand .brand-name{color:var(--white);font-size:22px;letter-spacing:1.5px;line-height:1}
.socials{left:868px;top:4316px;display:flex;gap:8px}
.socials span{width:36px;height:36px;border-radius:50%;border:2px solid var(--white)}
.copyright{left:0;top:4434px;width:1200px;text-align:center;color:var(--white);font-size:11px}
</style>
</head>
<body>

<!-- header -->
<div class="abs topline"></div>
<div class="abs topbar">CSLB LICENSE # 2418596 &nbsp;/&nbsp; info@summitbuildersca.example</div>
<div class="abs header-brand brand"><span class="brand-mark"></span><span class="brand-name">SUMMIT BUILDERS</span></div>
<nav class="abs mainnav"><span class="active">HOME</span><span>ABOUT US</span><span>SERVICES</span><span>PROJECTS</span><span>PORTFOLIO</span><span>CONTACT US</span></nav>

<!-- hero -->
<div class="abs hero-edge"></div>
<div class="abs hero" role="img" aria-label="Two builders in hard hats reviewing a tablet on a construction site"></div>
<h1 class="abs hero-title"><span class="l1">SUMMIT</span><span class="l2">BUILDERS</span></h1>
<div class="abs btn hero-btn">READ MORE</div>
<div class="abs dots"><span></span><span class="on"></span><span></span></div>

<!-- what we do -->
<h2 class="abs sec-title" style="top:972px">WHAT WE DO</h2>
<div class="abs sec-rule" style="top:1030px"></div>

<div class="abs card" style="left:111px;top:1077px">
  <div class="card-photo" role="img" aria-label="Timber frame of a house under construction" style="background:linear-gradient(180deg,#8fb6dc,#c9a27a 70%,#8c6a4a)"></div>
  <div class="card-icon"><svg width="38" height="38" viewBox="0 0 38 38" fill="none" stroke="#fff" stroke-width="2"><path d="M5 19 19 6l14 13M9 16v16h20V16"/><rect x="16" y="22" width="6" height="10"/></svg></div>
  <div class="card-body"><h3>Home Construction</h3><p>Sed ut perspiciatis unde omnis iste natus error sit voluptatem accusantium doloremque</p><div class="readmore">Read More <svg width="12" height="12" viewBox="0 0 12 12"><circle cx="6" cy="6" r="5" fill="none" stroke="currentColor" stroke-width="1.6"/><path d="M4 6h4M6.5 4.5 8 6 6.5 7.5" stroke="currentColor" fill="none" stroke-width="1.4"/></svg></div></div>
</div>
<div class="abs card active" style="left:444px;top:1077px">
  <div class="card-photo" role="img" aria-label="Bright remodeled kitchen with island" style="background:linear-gradient(180deg,#d8d6d2,#a8a29a 60%,#6f6a64)"></div>
  <div class="card-icon"><svg width="38" height="38" viewBox="0 0 38 38" fill="none" stroke="#fff" stroke-width="2"><rect x="9" y="6" width="20" height="26"/><path d="M13 11h4M21 11h4M13 17h4M21 17h4M13 23h4M21 23h4M6 32h26"/></svg></div>
  <div class="card-body"><h3>Building Remodeling</h3><p>Sed ut perspiciatis unde omnis iste natus error sit voluptatem accusantium doloremque</p><div class="readmore">Read More <svg width="12" height="12" viewBox="0 0 12 12"><circle cx="6" cy="6" r="5" fill="none" stroke="currentColor" stroke-width="1.6"/><path d="M4 6h4M6.5 4.5 8 6 6.5 7.5" stroke="currentColor" fill="none" stroke-width="1.4"/></svg></div></div>
</div>
<div class="abs card" style="left:775px;top:1077px">
  <div class="card-photo" role="img" aria-label="Modern open living and dining interior" style="background:linear-gradient(180deg,#c9c6c1,#8e8a84 55%,#5f5b58)"></div>
  <div class="card-icon"><svg width="38" height="38" viewBox="0 0 38 38" fill="none" stroke="#fff" stroke-width="2"><rect x="6" y="7" width="26" height="22"/><path d="M6 13h26M11 18h16M11 23h10M12 29v3M26 29v3"/></svg></div>
  <div class="card-body"><h3>Interior Design</h3><p>Sed ut perspiciatis unde omnis iste natus error sit voluptatem accusantium doloremque</p><div class="readmore">Read More <svg width="12" height="12" viewBox="0 0 12 12"><circle cx="6" cy="6" r="5" fill="none" stroke="currentColor" stroke-width="1.6"/><path d="M4 6h4M6.5 4.5 8 6 6.5 7.5" stroke="currentColor" fill="none" stroke-width="1.4"/></svg></div></div>
</div>

<div class="abs card" style="left:111px;top:1516px">
  <div class="card-photo" role="img" aria-label="Modern house exterior with patio at sunset" style="background:linear-gradient(180deg,#d9c49c,#b98a5a 55%,#5d4b36)"></div>
  <div class="card-icon"><svg width="38" height="38" viewBox="0 0 38 38" fill="none" stroke="#fff" stroke-width="2"><path d="M6 10h26M6 16h26M6 22h26M6 28h26M10 10v18M28 10v18"/></svg></div>
  <div class="card-body"><h3>Exterior Design</h3><p>Sed ut perspiciatis unde omnis iste natus error sit voluptatem accusantium doloremque</p><div class="readmore">Read More <svg width="12" height="12" viewBox="0 0 12 12"><circle cx="6" cy="6" r="5" fill="none" stroke="currentColor" stroke-width="1.6"/><path d="M4 6h4M6.5 4.5 8 6 6.5 7.5" stroke="currentColor" fill="none" stroke-width="1.4"/></svg></div></div>
</div>
<div class="abs card" style="left:444px;top:1516px">
  <div class="card-photo" role="img" aria-label="Room under renovation with exposed brick wall" style="background:linear-gradient(90deg,#8c7a6c,#c8c6c2 45%,#e2e0dc 75%,#a58663)"></div>
  <div class="card-icon"><svg width="38" height="38" viewBox="0 0 38 38" fill="none" stroke="#fff" stroke-width="2"><path d="M6 18 19 7l13 11M10 15v17h18V15"/><path d="M19 28v-8M15 22l4-4 4 4"/></svg></div>
  <div class="card-body"><h3>Renovations</h3><p>Sed ut perspiciatis unde omnis iste natus error sit voluptatem accusantium doloremque</p><div class="readmore">Read More <svg width="12" height="12" viewBox="0 0 12 12"><circle cx="6" cy="6" r="5" fill="none" stroke="currentColor" stroke-width="1.6"/><path d="M4 6h4M6.5 4.5 8 6 6.5 7.5" stroke="currentColor" fill="none" stroke-width="1.4"/></svg></div></div>
</div>
<div class="abs card" style="left:775px;top:1516px">
  <div class="card-photo" role="img" aria-label="Gloved hand holding a wrench at height" style="background:linear-gradient(135deg,#4a5566,#9aa4b0 50%,#3c4452)"></div>
  <div class="card-icon"><svg width="38" height="38" viewBox="0 0 38 38" fill="none" stroke="#fff" stroke-width="2"><circle cx="19" cy="19" r="13"/><circle cx="19" cy="19" r="5"/><path d="M19 6v8M19 24v8M6 19h8M24 19h8"/></svg></div>
  <div class="card-body"><h3>Safety</h3><p>Sed ut perspiciatis unde omnis iste natus error sit voluptatem accusantium doloremque</p><div class="readmore">Read More <svg width="12" height="12" viewBox="0 0 12 12"><circle cx="6" cy="6" r="5" fill="none" stroke="currentColor" stroke-width="1.6"/><path d="M4 6h4M6.5 4.5 8 6 6.5 7.5" stroke="currentColor" fill="none" stroke-width="1.4"/></svg></div></div>
</div>

<!-- who we are -->
<div class="abs who"></div>
<div class="abs who-photo" role="img" aria-label="Builders in hard hats working over blueprints on a table"></div>
<h2 class="abs who-title">WHO WE ARE</h2>
<p class="abs who-lead">We are rethoric question ran over her cheek When she reached the first hills of the Italic Mountains, she had a last view back on skyline of her hometown Bookmarksgrove, the headline</p>
<div class="abs feature" style="top:2237px">
  <div class="feature-icon"><svg width="50" height="50" viewBox="0 0 50 50" fill="none" stroke="#fff" stroke-width="2.2"><path d="M14 44V8M10 44h12M14 8l30 6M14 14h30M14 8l-8 6h8M38 14v8M35 22h6l-3 5"/><path d="M14 20l6-6M14 28l6-6"/></svg></div>
  <div><h4>WE'VE REPUTION FOR EXCELLENCE</h4><p>Hometown Bookmarksgrove, the headline of Alphabet Village and the subline..</p></div>
</div>
<div class="abs feature" style="top:2371px">
  <div class="feature-icon"><svg width="50" height="50" viewBox="0 0 50 50" fill="none" stroke="#fff" stroke-width="2.2"><path d="M14 20a11 11 0 0 1 22 0zM11 21h28"/><circle cx="25" cy="27" r="6"/><path d="M11 44c0-8 6-11 14-11s14 3 14 11z"/></svg></div>
  <div><h4>WE BUILD PARTNERSHIPS</h4><p>Hometown Bookmarksgrove, the headline of Alphabet Village and the subline..</p></div>
</div>

<!-- recent projects -->
<h2 class="abs sec-title" style="top:2583px">RECENT PROJECTS</h2>
<div class="abs sec-rule" style="top:2642px"></div>
<div class="abs proj" style="left:111px;top:2674px" role="img" aria-label="Two-storey suburban home with garage"><div class="proj-fill" style="background:linear-gradient(180deg,#6f9ccc,#b7a89a 55%,#5f7d3e)"></div></div>
<div class="abs proj" style="left:439px;top:2674px" role="img" aria-label="Villa beside a garden pond"><div class="proj-fill" style="background:linear-gradient(180deg,#9ac1e3,#c9b55a 45%,#4f8a3a 75%,#3f86b4)"></div></div>
<div class="abs proj" style="left:767px;top:2674px" role="img" aria-label="Modern high school building facade"><div class="proj-fill" style="background:linear-gradient(135deg,#d2c9bb,#b4ab9e 55%,#3e6fa3)"></div></div>
<div class="abs proj" style="left:111px;top:2944px" role="img" aria-label="Family house at dusk"><div class="proj-fill" style="background:linear-gradient(180deg,#5d7fb2,#8795b4 55%,#4d5870)"></div></div>
<div class="abs proj" style="left:439px;top:2944px" role="img" aria-label="Builders cutting timber with a power saw"><div class="proj-fill" style="background:linear-gradient(135deg,#c4a27e,#b58a5e 50%,#e0c27a)"></div></div>
<div class="abs proj" style="left:767px;top:2944px" role="img" aria-label="Engineers in hard hats looking up at a tower"><div class="proj-fill" style="background:linear-gradient(180deg,#2f5a9e,#6b8fc1 55%,#bcd24a)"></div></div>

<!-- clients -->
<div class="abs clients"></div>
<h2 class="abs sec-title" style="top:3320px">OUR CLIENTS</h2>
<div class="abs sec-rule" style="top:3380px"></div>
<div class="abs review" style="left:111px">
  <div class="review-head"><div class="avatar" role="img" aria-label="Portrait of client Alan Mercer"></div><div><h4>Alan Mercer</h4><div class="role">Chairman KRG</div></div><div class="stars">☆☆☆☆☆</div></div>
  <div class="review-body"><div class="quote">”</div><p>Wonderful work you and your crew are doing. Our team has nothing but good things to say - we are fortunate to have found you for this project!</p></div>
</div>
<div class="abs review" style="left:615px">
  <div class="review-head"><div class="avatar" role="img" aria-label="Portrait of client Rena Ortiz" style="background:radial-gradient(circle at 50% 40%,#d8b39a,#6e5446)"></div><div><h4>Rena Ortiz</h4><div class="role">Project Manager</div></div><div class="stars">☆☆☆☆☆</div></div>
  <div class="review-body"><div class="quote">”</div><p>SummitBuilders is one of the best general contractors we've worked with. The entire team tactfully of exceptional quality while staying</p></div>
</div>

<!-- stats -->
<div class="abs stats"></div>
<div class="abs stat" style="left:84px"><b>53</b><span>TOTAL PROJECT</span></div>
<div class="abs stat" style="left:339px"><b>371</b><span>STAFF MEMBERS</span></div>
<div class="abs stat" style="left:593px"><b>15</b><span>WORKING IN STATES</span></div>
<div class="abs stat" style="left:849px"><b>2,600</b><span>HOURS FOR WORK</span></div>

<!-- footer -->
<div class="abs footer"></div>
<nav class="abs footnav"><span>HOME</span><span>ABOUT US</span><span>SERVICES</span><span>PROJECTS</span><span>PORTFOLIO</span><span>CONTACT US</span></nav>
<div class="abs foot-rule"></div>

<h3 class="abs foot-title" style="left:113px;top:4136px">CONTACT US</h3>
<div class="abs field" style="left:111px;top:4191px;width:182px">First Name :</div>
<div class="abs field" style="left:302px;top:4191px;width:182px">Last Name :</div>
<div class="abs field" style="left:111px;top:4236px;width:182px">Email :</div>
<div class="abs field" style="left:302px;top:4236px;width:182px">Phone :</div>
<div class="abs field" style="left:111px;top:4281px;width:373px;height:52px">Message :</div>
<div class="abs btn submit">SUBMIT</div>

<h3 class="abs foot-title" style="left:562px;top:4136px">ADDRESS</h3>
<div class="abs info" style="top:4193px"><div class="info-icon"><svg width="16" height="20" viewBox="0 0 16 20" fill="none" stroke="#fff" stroke-width="1.8"><path d="M8 19s6-6.5 6-11A6 6 0 0 0 2 8c0 4.5 6 11 6 11z"/><circle cx="8" cy="8" r="2"/></svg></div><div><h5>ADDRESS</h5><p># Lorem Ipsum Dummy Lorem</p></div></div>
<div class="abs info" style="top:4255px"><div class="info-icon"><svg width="18" height="18" viewBox="0 0 18 18" fill="none" stroke="#fff" stroke-width="1.8"><path d="M4 1.5 7 5 5.5 7a9 9 0 0 0 5.5 5.5L13 11l3.5 3-2 2.5C8 16 2 10 1.5 3.5z"/></svg></div><div><h5>PHONE NUMBER</h5><p>000-121-1231</p></div></div>
<div class="abs info" style="top:4317px"><div class="info-icon"><svg width="18" height="14" viewBox="0 0 18 14" fill="none" stroke="#fff" stroke-width="1.8"><rect x="1" y="1" width="16" height="12"/><path d="m1 1 8 7 8-7"/></svg></div><div><h5>EMAIL US</h5><p>info@summitbuildersca.example</p></div></div>

<div class="abs foot-brand"><div class="brand-mark"></div><span class="brand-name">SUMMIT BUILDERS</span></div>
<div class="abs socials"><span></span><span></span><span></span><span></span><span></span></div>

<div class="abs copyright">© Copyright 2020 Summit Builders.All Rights Reserved</div>

</body>
</html>
```